Keystone Trench Co Business Card*

Looking for a professional, clean and crisp business card

I am in the underground utilities industry and am just looking for a really impressive business card. I would like our card to be white with our symbol crisp and clear with it protruding. I also have a business partner that will require his name and info on the card once the design is set. I would like to have our website info on the card which is;
http://keystonetrenchco.example/

Contact Information for Business Card

Website, contact name, number and email

```html
<!DOCTYPE html>
<html lang="en">
<head>
<meta charset="utf-8">
<title>Keystone Trench Co – Business Card</title>
<link rel="stylesheet" href="https://fonts.googleapis.com/css2?family=Roboto:wght@400;500&display=swap">
<style>
  :root {
    --bg: #e8e8e8;
    --card: #2b2b2b;
    --card-deep: #1f1f1f;
    --white: #ffffff;
    --muted: #c9c9c9;
    --blue: #3a63c0;
    --divider: #6b6b6b;
    --pattern-dark: #242424;
    --pattern-light: #9a9a9a;
  }
  * { box-sizing: border-box; margin: 0; padding: 0; }
  html, body { width: 1200px; height: 801px; overflow: hidden; }
  body {
    background: var(--bg);
    font-family: "Roboto", sans-serif;
    display: flex;
    align-items: center;
    justify-content: center;
    gap: 60px;
  }
  .card {
    position: relative;
    width: 520px;
    height: 297px;
    background: var(--card);
    border-bottom: 4px solid var(--blue);
    box-shadow: 0 10px 24px rgba(0,0,0,.22);
    overflow: hidden;
  }

  /* Front */
  .brand-mark {
    position: absolute;
    top: 58px;
    left: 0;
    right: 0;
    display: flex;
    align-items: center;
    justify-content: center;
    gap: 12px;
  }
  .brand-mark__dot {
    width: 22px;
    height: 22px;
    border-radius: 50%;
    background: var(--blue);
  }
  .brand-mark__name {
    color: var(--white);
    font-weight: 500;
    font-size: 30px;
    letter-spacing: .5px;
  }
  .front__details {
    position: absolute;
    left: 0;
    right: 0;
    bottom: 56px;
    display: flex;
    align-items: center;
    justify-content: center;
  }
  .person {
    text-align: right;
    padding-right: 18px;
  }
  .person__name {
    color: var(--blue);
    font-size: 21px;
    font-weight: 500;
  }
  .person__role {
    color: var(--muted);
    font-size: 13px;
    margin-top: 2px;
  }
  .details__divider {
    width: 1px;
    height: 58px;
    background: var(--divider);
  }
  .contact {
    list-style: none;
    padding-left: 18px;
  }
  .contact__item {
    display: flex;
    align-items: center;
    gap: 8px;
    color: var(--muted);
    font-size: 12.5px;
    line-height: 20px;
  }
  .contact__icon { width: 11px; height: 11px; flex: none; }

  /* Back */
  .back__pattern {
    position: absolute;
    inset: 0;
    background: linear-gradient(110deg, var(--pattern-dark) 0%, var(--pattern-dark) 40%, #4a4a4a 70%, var(--pattern-light) 100%);
  }
  .back__brand {
    position: absolute;
    left: 34px;
    bottom: 40px;
    color: var(--white);
    font-weight: 500;
    font-size: 24px;
  }
</style>
</head>
<body>

  <section class="card card--front" aria-label="Card front">
    <div class="brand-mark">
      <span class="brand-mark__dot"></span>
      <span class="brand-mark__name">Keystone Trench Co</span>
    </div>

    <div class="front__details">
      <div class="person">
        <p class="person__name">Dane Holloway</p>
        <p class="person__role">Owner</p>
      </div>
      <span class="details__divider"></span>
      <ul class="contact">
        <li class="contact__item">
          <svg class="contact__icon" viewBox="0 0 12 12" fill="#3a63c0"><path d="M2.5 1 4.5 3 3.6 4.4c.7 1.6 2 2.9 3.6 3.6L8.6 7.1l2 2-1.2 1.6C5.4 10.4 1.3 6.3 1 2.2z"/></svg>
          555-014-3473(DIGS)
        </li>
        <li class="contact__item">
          <svg class="contact__icon" viewBox="0 0 12 12" fill="none" stroke="#3a63c0" stroke-width="1.3"><rect x="1" y="2.5" width="10" height="7"/><path d="M1 2.5l5 4 5-4"/></svg>
          Dane@keystonetrenchco.example
        </li>
        <li class="contact__item">
          <svg class="contact__icon" viewBox="0 0 12 12" fill="none" stroke="#3a63c0" stroke-width="1.2"><circle cx="6" cy="6" r="5"/><path d="M1 6h10M6 1c-2.5 3-2.5 7 0 10M6 1c2.5 3 2.5 7 0 10"/></svg>
          www.keystonetrenchco.example
        </li>
      </ul>
    </div>
  </section>

  <section class="card card--back" aria-label="Card back">
    <div class="back__pattern" role="img" aria-label="Repeating pattern of mountain peaks fading from black to grey, with one blue peak"></div>
    <p class="back__brand">Keystone Trench Co</p>
  </section>

</body>
</html>
```